Fitness Business Card Design Needed

We are looking for a business card design that stands out but is also simple and unique. I like the idea of on one side using the picture of myself with my logo at my feet. I love the texture on the business card so please take that into account when designing. Then on the other side having my contact details. I want it to be clean, modern, and pretty. I am open to designs that allow spot gloss or gold foiling.

Contact Information for Business Card

Space for Name, Phone number, email, and website

```html
<!DOCTYPE html>
<html lang="en">
<head>
<meta charset="utf-8">
<title>Harlow Fitness – Business Card</title>
<link href="https://fonts.googleapis.com/css2?family=Roboto:wght@400;700&display=swap" rel="stylesheet">
<style>
  :root {
    --page: #2a2a2c;
    --gold-light: #eab868;
    --gold-mid: #c79a55;
    --gold-dark: #9c7a45;
    --gold-ink: #b8893f;
    --white: #ffffff;
  }
  * { box-sizing: border-box; margin: 0; padding: 0; }
  html, body { width: 1200px; height: 801px; overflow: hidden; }
  body {
    background: var(--page);
    font-family: "Roboto", Arial, sans-serif;
    position: relative;
  }
  .card {
    position: absolute;
    width: 540px;
    height: 309px;
    overflow: hidden;
    box-shadow: 0 10px 24px rgba(0,0,0,.45);
  }
  .card--contact { left: 600px; top: 70px; }
  .card--portrait {
    left: 70px; top: 420px;
    background: radial-gradient(ellipse at 40% 35%, var(--gold-light) 0%, var(--gold-mid) 45%, var(--gold-dark) 100%);
  }
  .card__bg { position: absolute; inset: 0; }

  .brand-name {
    position: absolute;
    font-family: "Roboto", Arial, sans-serif;
    font-weight: 400;
    font-size: 17px;
    letter-spacing: 3px;
    white-space: nowrap;
    text-align: center;
  }
  .card--contact .brand-name { left: 40px; top: 150px; width: 230px; color: var(--gold-ink); }
  .card--portrait .brand-name { left: 150px; top: 256px; width: 240px; color: var(--white); }

  .identity {
    position: absolute; right: 34px; top: 44px;
    text-align: right; color: var(--white);
  }
  .identity__name { font-size: 22px; font-weight: 700; letter-spacing: .5px; }
  .identity__role { font-size: 13px; letter-spacing: .6px; }

  .contact {
    position: absolute; right: 34px; top: 180px;
    text-align: right; color: var(--white); font-size: 13px; line-height: 18px;
  }
  .contact__address { margin-bottom: 8px; }
  .contact__row { display: flex; justify-content: flex-end; align-items: center; gap: 10px; }
  .contact__icon { width: 12px; height: 12px; fill: var(--white); }

  .portrait {
    position: absolute; left: 215px; top: 24px; width: 110px; height: 210px;
    border-radius: 40px 40px 12px 12px;
    background: linear-gradient(180deg, #d9a47a 0%, #c9816a 45%, #b97b5c 100%);
  }
</style>
</head>
<body>

<section class="card card--contact">
  <svg class="card__bg" viewBox="0 0 540 309" preserveAspectRatio="none">
    <defs>
      <radialGradient id="goldGlow" cx="0.72" cy="0.45" r="0.7">
        <stop offset="0" stop-color="#eab868"/>
        <stop offset="0.5" stop-color="#c79a55"/>
        <stop offset="1" stop-color="#9c7a45"/>
      </radialGradient>
    </defs>
    <rect width="540" height="309" fill="url(#goldGlow)"/>
    <polygon points="0,0 240,0 330,150 130,309 0,309" fill="#ffffff"/>
    <polyline points="252,0 344,150 144,309" fill="none" stroke="#ffffff" stroke-width="2"/>
  </svg>

  <p class="brand-name">HARLOW FITNESS</p>

  <div class="identity">
    <p class="identity__name">DANA WHITLEY</p>
    <p class="identity__role">FITNESS TRAINER</p>
  </div>

  <div class="contact">
    <p class="contact__address">1420 Birchwood Avenue<br>Juneau, Alaska 34512</p>
    <p class="contact__row">555 210 7734
      <svg class="contact__icon" viewBox="0 0 24 24"><path d="M6.6 10.8a15 15 0 0 0 6.6 6.6l2.2-2.2a1 1 0 0 1 1-.25 11.4 11.4 0 0 0 3.6.57 1 1 0 0 1 1 1V20a1 1 0 0 1-1 1A17 17 0 0 1 3 4a1 1 0 0 1 1-1h3.5a1 1 0 0 1 1 1c0 1.25.2 2.45.57 3.57a1 1 0 0 1-.25 1z"/></svg>
    </p>
    <p class="contact__row">hello@harlowfitness.com
      <svg class="contact__icon" viewBox="0 0 24 24"><path d="M2 5h20v14H2z M2 5l10 8 10-8" fill="none" stroke="#fff" stroke-width="2"/></svg>
    </p>
    <p class="contact__row">www.harlowfitness.com
      <svg class="contact__icon" viewBox="0 0 24 24"><circle cx="12" cy="12" r="9" fill="none" stroke="#fff" stroke-width="2"/><path d="M3 12h18M12 3c3 3 3 15 0 18M12 3c-3 3-3 15 0 18" fill="none" stroke="#fff" stroke-width="1.5"/></svg>
    </p>
  </div>
</section>

<section class="card card--portrait">
  <div class="portrait" role="img" aria-label="Full-length photo of the trainer standing on a patch of sand"></div>
  <p class="brand-name">HARLOW FITNESS</p>
</section>

</body>
</html>
```